Website for New Phone Company

Our company "Lagoonstar Telecom" requires a new web-site.

We enable Pacific Islanders (Fijians, Samoans, Tongans) to speak to their friends and family back home for a fraction of the cost of other phone companies whilst maintaining a quality. Our target audience is price sensitive but is demanding with quality, we would like them to gather a feel that they are dealing with a safe company that is orientated towards the Pacific Island community, has low pricing and yet doesn't compromise on quality.

We are going to be marketing via online channels and so a Zarnik friendly web-site is important. We essentially need three pages designed which we will use with our content.

Page 1 - Homepage Lagoonstar Telecom - Our prime brand is Lagoonstar Telecom and we would like to promote this brand on our web-site.

However, we have three plans under this brand called Verami, Kelipo and Musendi. We would like the main page to have three unique service offerings for Musendi, Kelipo and Verami. Something along the lines of being able to choose a plan down on the page. I would like to give examples here of companies in our industry that are extremely successful in this trade i.e. www.ringbeam.co.nz, www.9voxa.co.nz, www.pelquix.com

The objective of this design is to present the customer with three unique offerings targeted to Samoa (Musendi), Kelipo (Tonga) and Verami (Fiji).

Page 2 - Content/Template Page for Lagoonstar Telecom - We require a page where we can place content like About Us, Contact Us etc.

Page 3 - We require a single design that will fit all three brands as per the brand images attached for Verami, Musendi and Kelipo. This will almost be used as a landing page to brand the plan exclusively under our company. All three plans / service offerings are being marketed under "Lagoonstar Telecom" which makes it important to use both the service offering logo as well as the company logo. This page needs to act more as a promotional page where it promotes our service offering. e.g. Call Samoa from only 50c a minute type of thing.

The objective of the design of the landing / service offering page is to entice the customer to act upon the offer by joining our organisation.

We will be available throughout the process to guide you better.
Updates

Project Deadline Extended
Reason: We haven't received suitable designs to choose from. We would like to see quality work not quantity.

Industry/Entity Type

It Company

```html
<!DOCTYPE html>
<html lang="en">
<head>
<meta charset="utf-8">
<title>Lagoonstar Telecom</title>
<link rel="stylesheet" href="https://fonts.googleapis.com/css2?family=Anton&family=Oswald:wght@400;500&family=Open+Sans:wght@400;700&display=swap">
<style>
:root{
  --red:#d3161b;
  --red-light:#ef4b45;
  --ink:#2b2b2b;
  --grey:#9a9a9a;
  --grey-dark:#6d6e71;
  --line:#d2d2d2;
  --band:#f0f0f0;
  --footer:#333333;
  --verami:#c8452a;
  --musendi:#8dc63f;
  --kelipo:#4fa83a;
}
*{box-sizing:border-box;margin:0;padding:0}
html,body{width:1028px;height:1200px;overflow:hidden;background:#fff}
body{position:relative;font-family:Arial,Helvetica,sans-serif;color:var(--ink)}
.abs{position:absolute}

.site-header{position:absolute;left:0;top:0;width:1028px;height:77px;border-top:2px solid var(--red);background:#fff}
.brand{position:absolute;left:150px;top:14px;display:flex;align-items:center;gap:10px}
.brand-dot{width:44px;height:44px;border-radius:50%;background:var(--red)}
.brand-name{font-family:"Open Sans",sans-serif;font-weight:700;font-size:23px;color:var(--grey-dark);letter-spacing:-.3px}

.social{position:absolute;top:15px;left:694px;display:flex;align-items:center;gap:18px;font-size:8.5px;color:#333}
.social-item{display:flex;align-items:center;gap:4px}
.social-square{width:13px;height:13px;background:#3b5998}
.social-square.blue{background:#35a6e0}
.plus-one{border:1px solid #ccc;padding:1px 4px;color:var(--red);font-weight:bold}
.plus-count{border:1px solid #ccc;padding:1px 4px;color:#666}

.main-nav{position:absolute;top:50px;left:570px;display:flex;gap:0;font-size:9.5px;font-weight:bold;color:#222}
.main-nav a{color:inherit;text-decoration:none;padding:3px 9px;margin-right:12px;border-radius:4px}
.main-nav a.active{background:var(--red);color:#fff}

.hero{position:absolute;left:0;top:77px;width:1028px;height:355px;
  background:linear-gradient(180deg,#2f72c0 0%,#6ea9dd 30%,#cfe3f1 52%,#1c9fb4 58%,#5cc3c5 66%,#e9ecec 76%,#dedcd6 100%)}
.hero-title{position:absolute;left:414px;top:72px;font-family:"Anton",sans-serif;font-size:34px;color:#fff;letter-spacing:.2px;text-shadow:0 1px 3px rgba(0,0,0,.35)}

.plan{position:absolute;top:457px;width:236px;height:330px;border:1px solid var(--line);background:#fff;text-align:center;font-family:"Oswald",sans-serif}
.plan-mark{margin:22px auto 0;width:62px;height:62px;border-radius:50%}
.plan-name{margin-top:8px;font-family:"Oswald",sans-serif;font-weight:500;font-size:28px;letter-spacing:1px;line-height:1}
.plan-valid{margin-top:17px;font-size:19px;color:var(--grey);line-height:1}
.plan-price{margin-top:10px;font-size:40px;font-weight:500;color:var(--ink);line-height:1}
.plan-period{margin-top:4px;font-size:19px;color:var(--grey);line-height:1}
.buy-btn{display:block;margin:17px auto 0;width:178px;height:40px;border-radius:4px;background:linear-gradient(180deg,var(--red-light),var(--red));color:#fff;font-size:20px;line-height:40px;text-decoration:none;box-shadow:0 1px 2px rgba(0,0,0,.25)}
.read-more{display:block;margin-top:14px;font-size:19px;color:#1c1c1c;text-decoration:none}

.spotlight{position:absolute;left:0;top:816px;width:1028px;height:182px;background:var(--band);border-top:1px solid #e2e2e2;border-bottom:1px solid #e2e2e2}
.section-title{position:absolute;width:100%;text-align:center;font-family:"Open Sans",sans-serif;font-size:19px;color:#333}
.news{position:absolute;top:70px;width:370px;display:flex;gap:17px;font-family:"Open Sans",sans-serif}
.news-date{flex:none;width:40px;height:45px;background:#c7c7c7;color:#fff;text-align:center;line-height:1}
.news-date .m{display:block;font-size:10px;padding-top:5px}
.news-date .d{display:block;font-size:20px;padding-top:2px}
.news-title{font-size:13px;font-weight:700;color:var(--red);margin-top:5px}
.news-text{margin-top:4px;font-size:8.6px;line-height:15px;color:#555;width:306px}

.partners-title{top:1022px}
.partner{position:absolute;top:1074px;height:48px;border:1px solid #dcdcdc;background:#fff;display:flex;align-items:center;justify-content:center}
.partner-shape{width:80px;height:24px;border-radius:4px}
.partner.featured{background:linear-gradient(180deg,#3d5f8d,#9fb6cc 50%,#3d5f8d)}
.carousel-arrow{position:absolute;top:1088px}

.site-footer{position:absolute;left:0;top:1164px;width:1028px;height:36px;background:var(--footer);color:#ddd;font-size:7.5px;padding:14px 0 0 124px}
</style>
</head>
<body>

<header class="site-header">
  <div class="brand"><span class="brand-dot"></span><span class="brand-name">Lagoonstar Telecom</span></div>
  <div class="social">
    <span class="social-item"><span class="plus-one">Zarnik +1</span><span class="plus-count">1</span></span>
    <span class="social-item"><span class="social-square"></span>Join us</span>
    <span class="social-item"><span class="social-square blue"></span>Follow us</span>
  </div>
  <nav class="main-nav">
    <a class="active" href="#">HOME</a><a href="#">ABOUT US</a><a href="#">PLANS</a><a href="#">RECHARGE</a><a href="#">CONTACT</a>
  </nav>
</header>

<section class="hero" role="img" aria-label="Couple holding hands on a white sand beach under a palm tree, looking at a turquoise sea">
  <h1 class="hero-title">Connecting you with the Pacific.</h1>
</section>

<article class="plan" style="left:124px">
  <div class="plan-mark" style="background:var(--verami)"></div>
  <div class="plan-name" style="color:var(--verami)">VERAMI</div>
  <div class="plan-valid">valid for 1 year</div>
  <div class="plan-price">$7.79</div>
  <div class="plan-period">per month</div>
  <a class="buy-btn" href="#">Buy Now</a>
  <a class="read-more" href="#">read more</a>
</article>
<article class="plan" style="left:384px">
  <div class="plan-mark" style="background:var(--musendi)"></div>
  <div class="plan-name" style="color:var(--musendi)">Musendi</div>
  <div class="plan-valid">valid for 1 year</div>
  <div class="plan-price">$9.79</div>
  <div class="plan-period">per month</div>
  <a class="buy-btn" href="#">Buy Now</a>
  <a class="read-more" href="#">read more</a>
</article>
<article class="plan" style="left:643px">
  <div class="plan-mark" style="background:var(--kelipo)"></div>
  <div class="plan-name" style="color:var(--kelipo)">Kelipo</div>
  <div class="plan-valid">valid for 1 year</div>
  <div class="plan-price">$11.79</div>
  <div class="plan-period">per month</div>
  <a class="buy-btn" href="#">Buy Now</a>
  <a class="read-more" href="#">read more</a>
</article>

<section class="spotlight">
  <h2 class="section-title" style="top:14px">In the Spotlight</h2>
  <div class="news" style="left:127px">
    <div class="news-date"><span class="m">SEP</span><span class="d">14</span></div>
    <div>
      <h3 class="news-title">Voluptatem accusantium</h3>
      <p class="news-text">Aut perspiciatis unde omnis istnatus sit voluptatem accusantiumedel doloreque laudantium, totam rem aperiam, eaque ipssi architectori beatae vitae dicta. Aut perspiciatis unde omnis istnatus sit voluptatem accusantiumedel doloreque laudantium, totam rem aperiam, eaque ipssi architectori beatae vitae dicta.</p>
    </div>
  </div>
  <div class="news" style="left:512px;top:66px">
    <div class="news-date"><span class="m">SEP</span><span class="d">14</span></div>
    <div>
      <h3 class="news-title">Voluptatem accusantium</h3>
      <p class="news-text">Aut perspiciatis unde omnis istnatus sit voluptatem accusantiumedel doloreque laudantium, totam rem aperiam, eaque ipssi architectori beatae vitae dicta. Aut perspiciatis unde omnis istnatus sit voluptatem accusantiumedel doloreque laudantium, totam rem aperiam, eaque ipssi architectori beatae vitae dicta.</p>
    </div>
  </div>
</section>

<h2 class="section-title partners-title">Our Partners</h2>
<svg class="carousel-arrow" style="left:134px" width="10" height="16" viewBox="0 0 10 16"><path d="M8 2 L2 8 L8 14" fill="none" stroke="#bbb" stroke-width="2"/></svg>
<div class="partner" style="left:162px;width:128px"><span class="partner-shape" style="background:#2a7fc9"></span></div>
<div class="partner" style="left:301px;width:129px"><span class="partner-shape" style="background:#d8232a"></span></div>
<div class="partner featured" style="left:439px;width:127px"><span class="partner-shape" style="background:#e6edf3"></span></div>
<div class="partner" style="left:577px;width:129px"><span class="partner-shape" style="background:#2a7fc9"></span></div>
<div class="partner" style="left:716px;width:128px"><span class="partner-shape" style="background:#d8232a"></span></div>
<svg class="carousel-arrow" style="left:859px" width="10" height="16" viewBox="0 0 10 16"><path d="M2 2 L8 8 L2 14" fill="none" stroke="#666" stroke-width="2"/></svg>

<footer class="site-footer">Copyright 2014 Lagoonstar Telecom, All rights reserved.</footer>

</body>
</html>
```